RWT Fittings Ltd Business Cards

We need a business card with our business logo. We provide window and door installations on high-rises in west coast British Colombia, Canada.

I would like my business information and details on one side of the card, and the other side the company name with logo

Target Market(s)

General Contractors

Industry/Entity Type

Construction

Contact Information for Business Card

one side i want my company name and logo in the dark theme logo that i provided

Requirements
Must have
• Marco Peltieri, 16045518293, RWTFittings@mailbox-demo.com, 1407-5194 Linden Row Burnaby BC, V5H 2K9, Owner & Manager

```html
<!DOCTYPE html>
<html lang="en">
<head>
<meta charset="utf-8">
<title>RWT Fittings Ltd Business Cards</title>
<link rel="stylesheet" href="https://fonts.googleapis.com/css2?family=Lato:wght@400;700&display=swap">
<style>
  :root {
    --stage: #2a2a2c;
    --card-dark: #2e2a28;
    --card-dark-2: #423c38;
    --card-light: #ffffff;
    --brand-blue: #29a9e1;
    --ink-grey: #6b6b6b;
    --band-grey: #9a9a9a;
    --rule-blue: #4bb4e6;
  }
  * { box-sizing: border-box; margin: 0; padding: 0; }
  html, body { width: 1200px; height: 900px; overflow: hidden; }
  body {
    background: var(--stage);
    font-family: "Lato", sans-serif;
    position: relative;
  }
  .card {
    position: absolute;
    left: 300px;
    width: 600px;
    height: 343px;
    border-radius: 18px;
    overflow: hidden;
  }
  /* Logo side */
  .card-back { top: 62px; background: var(--card-dark); }
  .card-back .backdrop {
    position: absolute; inset: 0;
    background: radial-gradient(ellipse at 70% 40%, var(--card-dark-2) 0%, var(--card-dark) 70%);
  }
  .brand-lockup {
    position: absolute; left: 0; right: 0; top: 0; bottom: 0;
    display: flex; align-items: center; justify-content: center; gap: 16px;
  }
  .brand-mark { width: 38px; height: 38px; background: var(--brand-blue); }
  .brand-name {
    font-weight: 700; font-size: 40px; color: var(--brand-blue);
    letter-spacing: 1px;
  }
  /* Info side */
  .card-front { top: 470px; background: var(--card-light); }
  .person { position: absolute; left: 40px; top: 58px; }
  .person-name {
    font-weight: 700; font-size: 27px; color: var(--brand-blue);
    text-transform: uppercase; letter-spacing: 0.5px;
  }
  .person-title { font-size: 16px; color: var(--ink-grey); margin-top: 2px; }
  .divider {
    position: absolute; left: 40px; right: 40px; top: 140px;
    height: 1px; background: var(--rule-blue);
  }
  .contact-list { position: absolute; left: 40px; top: 160px; list-style: none; }
  .contact-list li {
    display: flex; align-items: center; gap: 12px;
    font-size: 15px; color: var(--ink-grey); height: 27px;
  }
  .contact-list svg { width: 14px; height: 14px; fill: var(--brand-blue); flex: none; }
  .front-brand {
    position: absolute; right: 40px; top: 62px;
    display: flex; align-items: center; gap: 10px;
  }
  .front-brand .brand-mark { width: 24px; height: 24px; }
  .front-brand .brand-name { font-size: 26px; }
  .company-block {
    position: absolute; right: 40px; top: 168px; text-align: right;
    font-size: 15px; color: var(--ink-grey); line-height: 1.5;
  }
  .company-block .company-name { color: var(--brand-blue); font-weight: 700; font-size: 16px; }
  .edge-band { position: absolute; left: 0; bottom: 0; width: 600px; height: 20px; }
</style>
</head>
<body>
  <section class="card card-back" aria-label="Logo side">
    <div class="backdrop" role="img" aria-label="Softly blurred office interior behind the company name"></div>
    <div class="brand-lockup">
      <span class="brand-mark"></span>
      <span class="brand-name">RWT Fittings Ltd</span>
    </div>
  </section>

  <section class="card card-front" aria-label="Contact side">
    <div class="person">
      <div class="person-name">Marco Peltieri</div>
      <div class="person-title">Owner &amp; Manager</div>
    </div>
    <div class="front-brand">
      <span class="brand-mark"></span>
      <span class="brand-name">RWT Fittings Ltd</span>
    </div>
    <div class="divider"></div>
    <ul class="contact-list">
      <li><svg viewBox="0 0 24 24"><path d="M6.6 10.8a15 15 0 0 0 6.6 6.6l2.2-2.2c.3-.3.7-.4 1-.2 1.1.4 2.3.6 3.6.6.6 0 1 .4 1 1V20c0 .6-.4 1-1 1A17 17 0 0 1 3 4c0-.6.4-1 1-1h3.5c.6 0 1 .4 1 1 0 1.3.2 2.5.6 3.6.1.3 0 .7-.2 1z"/></svg>+1 604 551 8293</li>
      <li><svg viewBox="0 0 24 24"><path d="M7 1h10a2 2 0 0 1 2 2v18a2 2 0 0 1-2 2H7a2 2 0 0 1-2-2V3a2 2 0 0 1 2-2zm0 3v14h10V4z"/></svg>+1 604 551 8293</li>
      <li><svg viewBox="0 0 24 24"><path d="M6 2h12v5H6zM3 8h18a2 2 0 0 1 2 2v7h-4v5H5v-5H1v-7a2 2 0 0 1 2-2zm4 8v4h10v-4z"/></svg>+1 604 551 8293</li>
      <li><svg viewBox="0 0 24 24"><path d="M2 5h20v14H2zm2 2v.5l8 5 8-5V7l-8 5z"/></svg>RWTFittings@mailbox-demo.com</li>
    </ul>
    <div class="company-block">
      <div class="company-name">RWT Fittings Ltd</div>
      <div>1407-5194 Linden Row</div>
      <div>Burnaby BC, V5H 2K9</div>
      <div>www.rwtfittings-demo.com</div>
    </div>
    <svg class="edge-band" viewBox="0 0 600 20" preserveAspectRatio="none" aria-hidden="true">
      <polygon points="0,0 380,0 366,20 0,20" fill="var(--brand-blue)"/>
      <polygon points="392,0 600,0 600,20 378,20" fill="var(--band-grey)"/>
    </svg>
  </section>
</body>
</html>
```